Financial Advisor Resource Firm needs business card design

Need business card design for company in Omaha NE called Meridale Circle. We provide resources to financial advisors....workshop programs, retirement analysis, and insurance planning. I would like to see designs that use grays, greens, black, and white colors. The final design should communicate 'collaboration' and be simple yet attractive to financial planning clients. I will attached our logo and another picture of a puzzle piece coming together. I would like the incorporate the puzzle picture somehow, maybe on the back somehow, with color or just the gray scale....OR, the picture be the front of the card with 'Meridale' definition on it (see upload) and then company logo, employee name, title, address on the back (see ppt uploaded). The following disclosure needs to be included somewhere- Advisory services offered through Stonebrook Assets, LLC.
Updates

I uploaded a svg and ai file of the logo

Target Market(s)

Financial planning clients and financial advisors....so pretty diverse age range of about 40-70.

Industry/Entity Type

Financial Planning

Contact Information for Business Card

Tobias L. Fenwright, MBA
Founder/President
5287 E. Larkin Road
Suite 230
Omaha, NE 68190
Phone- (402) 555-0147
Cell- (402) 555-0183
Fax- (402) 555-0129
email- tobias@meridaleplan.example
web address- www.meridaleplan.example

Colors
1b1b1b
474747
d3d3d3
ffffff
9bcb3c
abd036

Requirements
Must have
• Must include logo provided, must be 2 sided, and must have disclosure...all of these items listed in project description

```html
<!DOCTYPE html>
<html lang="en">
<head>
<meta charset="utf-8">
<title>Meridale Circle — Business Card</title>
<link href="https://fonts.googleapis.com/css2?family=Roboto:wght@400;500;700&display=swap" rel="stylesheet">
<style>
  :root {
    --ink: #1b1b1b;
    --graphite: #474747;
    --silver: #d3d3d3;
    --paper: #ffffff;
    --leaf: #9bcb3c;
    --lime: #abd036;
    --stage: #ecebe8;
    --photo-dark: #6f6f6f;
    --photo-light: #a9a9a9;
  }
  html, body {
    margin: 0;
    width: 1200px;
    height: 900px;
    overflow: hidden;
    background: var(--stage);
    font-family: "Roboto", Arial, sans-serif;
  }
  .canvas {
    position: relative;
    width: 1200px;
    height: 900px;
  }
  .card {
    position: absolute;
    left: 250px;
    width: 700px;
    height: 400px;
    overflow: hidden;
    box-shadow: 0 6px 18px rgba(0,0,0,0.18);
  }
  .card--back { top: 30px; }
  .card--front { top: 470px; background: var(--paper); }

  /* Back */
  .back-photo {
    position: absolute;
    inset: 0;
    background: radial-gradient(ellipse at 65% 40%, var(--photo-light) 0%, #8c8c8c 45%, var(--photo-dark) 100%);
  }
  .back-brand {
    position: absolute;
    left: 0; right: 0;
    top: 150px;
    text-align: center;
    color: var(--paper);
    font-weight: 500;
    font-size: 50px;
    letter-spacing: 3px;
    opacity: 0.9;
  }
  .back-disclosure {
    position: absolute;
    left: 0; right: 0;
    top: 250px;
    text-align: center;
    color: var(--paper);
    font-size: 15px;
    letter-spacing: 0.4px;
    opacity: 0.9;
  }

  /* Front */
  .front-brand {
    position: absolute;
    left: 40px;
    top: 138px;
    display: flex;
    align-items: center;
    gap: 10px;
    color: var(--ink);
    font-weight: 500;
    font-size: 31px;
    letter-spacing: 1px;
  }
  .front-brand__dot {
    width: 18px; height: 18px;
    border-radius: 50%;
    background: var(--leaf);
  }
  .divider {
    position: absolute;
    left: 355px;
    top: 150px;
    width: 1px;
    height: 135px;
    background: var(--silver);
  }
  .name-accent {
    position: absolute;
    left: 375px;
    top: 62px;
    width: 4px;
    height: 44px;
    background: var(--leaf);
  }
  .person {
    position: absolute;
    left: 395px;
    top: 60px;
  }
  .person__name {
    margin: 0;
    color: var(--leaf);
    font-weight: 700;
    font-size: 21px;
  }
  .person__title {
    margin: 2px 0 0;
    color: var(--graphite);
    font-size: 15px;
  }
  .address {
    position: absolute;
    left: 385px;
    top: 140px;
    margin: 0;
    color: var(--graphite);
    font-size: 15px;
    line-height: 21px;
    font-style: normal;
  }
  .contacts {
    position: absolute;
    left: 385px;
    top: 200px;
    margin: 0;
    padding: 0;
    list-style: none;
    color: var(--graphite);
    font-size: 15px;
  }
  .contacts li {
    display: flex;
    align-items: center;
    gap: 10px;
    height: 22px;
  }
  .contacts svg { width: 12px; height: 12px; fill: var(--leaf); }
  .band {
    position: absolute;
    left: 0;
    bottom: 0;
    width: 700px;
    height: 80px;
  }
  .band__url {
    position: absolute;
    left: 0; right: 0;
    bottom: 22px;
    text-align: center;
    color: var(--paper);
    font-weight: 500;
    font-size: 15px;
    letter-spacing: 1px;
  }
</style>
</head>
<body>
<main class="canvas">

  <section class="card card--back" aria-label="Card back">
    <div class="back-photo" role="img" aria-label="Grayscale photo of hands fitting puzzle pieces together"></div>
    <div class="back-brand">Meridale Circle</div>
    <p class="back-disclosure">Advisory services offered through Stonebrook Assets, LLC</p>
  </section>

  <section class="card card--front" aria-label="Card front">
    <div class="front-brand">
      <span class="front-brand__dot"></span>
      <span>Meridale Circle</span>
    </div>

    <div class="divider"></div>
    <div class="name-accent"></div>

    <div class="person">
      <p class="person__name">Tobias L. Fenwright, MBA</p>
      <p class="person__title">Founder/President</p>
    </div>

    <address class="address">
      5287 E. Larkin Road<br>
      Suite 230, Omaha, NE 68190
    </address>

    <ul class="contacts">
      <li>
        <svg viewBox="0 0 12 12" aria-hidden="true"><path d="M2.5 0.5 L4.5 0.5 L5 3 L3.7 4 C4.4 5.6 6.4 7.6 8 8.3 L9 7 L11.5 7.5 L11.5 9.5 C11.5 10.8 10.5 11.5 9.5 11.5 C4.5 11.2 0.8 7.5 0.5 2.5 C0.5 1.5 1.2 0.5 2.5 0.5 Z"/></svg>
        (402) 555-0147
      </li>
      <li>
        <svg viewBox="0 0 12 12" aria-hidden="true"><path d="M3 0 H9 A1 1 0 0 1 10 1 V11 A1 1 0 0 1 9 12 H3 A1 1 0 0 1 2 11 V1 A1 1 0 0 1 3 0 Z M3.5 1.5 V9.5 H8.5 V1.5 Z"/></svg>
        (402) 555-0183
      </li>
      <li>
        <svg viewBox="0 0 12 12" aria-hidden="true"><path d="M3 0 H9 V3 H3 Z M1 4 H11 A1 1 0 0 1 12 5 V9 H9 V12 H3 V9 H0 V5 A1 1 0 0 1 1 4 Z M4 8 V11 H8 V8 Z"/></svg>
        (402) 555-0129
      </li>
      <li>
        <svg viewBox="0 0 12 12" aria-hidden="true"><path d="M0 2 H12 V10 H0 Z M1 3 V3.4 L6 6.8 L11 3.4 V3 Z"/></svg>
        tobias@meridaleplan.example
      </li>
    </ul>

    <svg class="band" viewBox="0 0 700 80" preserveAspectRatio="none" aria-hidden="true">
      <rect x="0" y="18" width="700" height="10" fill="var(--silver)"/>
      <rect x="0" y="28" width="700" height="16" fill="var(--graphite)" opacity="0.55"/>
      <rect x="0" y="44" width="700" height="4" fill="var(--leaf)"/>
      <path d="M0 48 H700 V80 H0 Z" fill="var(--paper)"/>
      <path d="M170 80 C205 80 200 22 245 22 H455 C500 22 495 80 530 80 Z" fill="var(--leaf)"/>
      <rect x="0" y="72" width="700" height="8" fill="var(--leaf)"/>
    </svg>
    <div class="band__url">www.meridaleplan.example</div>
  </section>

</main>
</body>
</html>
```